Business Cards for IT Consulting Company (Managed Service Provider)

I am looking to have some business cards printed and would like some designs. We are an IT Consulting company based in Vancouver BC. I would like a nice clean and modern look to the cards. I have uploaded all the versions of my logo so parts can be used as needed. Here is a snippit from our website homepage:

Quillbrook Networks Ltd. is an IT Solutions Partner located in Vancouver BC, Canada. We offer IT solutions and support to customers in the greater Vancouver Area. With expertise in Microsoft platforms, as well as Linux and Mac OSX and over 12 years experience in the IT industry, Quillbrook Networks is dedicated to offering our clients top quality service and products. We take pride in the solutions we offer our customers. The greatest compliment a client can give us is to recommend our services.

Quillbrook Networks Ltd. offers a wide range of IT services from onsite service to remote support and managed service solutions. This allows clients to choose the support path that best suits their company’s needs. Supporting many different sized companies from small to enterprise level over the past 12 years Quillbrook Networks has the experience and expertise needed to ensure things run smoothly. Allowing our clients to focus on doing business.

Revolutionizing the way IT services are delivered.

Quillbrook Networks is dedicated to providing our clients with IT solutions that work and grow with them for years to come. This philosophy helps save money in the long run instead of replacing equipment constantly. Far too often IT solutions are not well thought out and while possibly solving the problem at hand, require replacement due to growth or quality within a very short time frame. Quillbrook Networks takes pride in providing solutions that will last and be able to accommodate growth without the need for replacement.

Industry/Entity Type

Information Technology

Contact Information for Business Card

Quillbrook Networks Ltd.
(Employee Name)
Eml: (Employees Email Address)
Web: quillbrook.me
Ph: 604-555-0148

Font styles to use
Serif
Sans Serif

Requirements
Must have
• The Company logo and company colors.
Nice to have
• - Our tag line: "Revolutionizing IT Services" or "Revolutionizing the way IT services are delivered."
• - Also I really like the idea of nature and technology together blending which is sort of where my logo came from so integrating that somehow onto the business cards would be great.

```html
<!DOCTYPE html>
<html lang="en">
<head>
<meta charset="utf-8">
<title>Quillbrook Networks Ltd. — Business Cards</title>
<link href="https://fonts.googleapis.com/css2?family=Montserrat:wght@400;500;600&display=swap" rel="stylesheet">
<style>
  :root {
    --backdrop: #2b2b2b;
    --brand-blue: #35a8e0;
    --ink-grey: #4a4a4a;
    --paper: #ffffff;
    --rule: #9fd3ee;
  }
  * { margin: 0; padding: 0; box-sizing: border-box; }
  html, body {
    width: 1200px; height: 1114px; overflow: hidden;
    background: var(--backdrop);
    font-family: "Montserrat", sans-serif;
  }
  .canvas {
    position: relative; width: 1200px; height: 1114px;
  }
  .card {
    position: absolute; left: 280px;
    width: 640px; height: 366px;
    background: var(--paper);
    overflow: hidden;
  }
  .card--front { top: 150px; }
  .card--back { top: 598px; }

  /* Front card */
  .band { position: absolute; left: 0; width: 100%; background: var(--brand-blue); }
  .band--top { top: 0; height: 82px; }
  .band--bottom { bottom: 0; height: 96px; display: flex; align-items: center; justify-content: center; }
  .tagline {
    color: var(--paper); font-size: 17px; font-weight: 400; letter-spacing: 0.4px;
  }
  .wordmark {
    position: absolute; display: flex; align-items: center; gap: 16px;
  }
  .card--front .wordmark { left: 50%; top: 135px; transform: translateX(-50%); }
  .wordmark__square {
    width: 40px; height: 40px; background: var(--brand-blue); flex: none;
  }
  .wordmark__name {
    color: var(--brand-blue); font-weight: 600; line-height: 1.05;
  }
  .wordmark__name .primary { display: block; font-size: 46px; letter-spacing: -0.5px; }
  .wordmark__name .secondary { display: block; font-size: 17px; letter-spacing: 2.5px; }

  /* Back card */
  .card--back .wordmark { left: 48px; top: 150px; }
  .card--back .wordmark__name .primary { font-size: 38px; }
  .card--back .wordmark__name .secondary { font-size: 14px; letter-spacing: 2px; }
  .divider {
    position: absolute; left: 356px; top: 92px; width: 1.5px; height: 170px;
    background: linear-gradient(to bottom, transparent, var(--rule) 20%, var(--rule) 80%, transparent);
  }
  .contact { position: absolute; left: 378px; top: 100px; color: var(--ink-grey); }
  .contact__name { color: var(--brand-blue); font-weight: 600; font-size: 18px; }
  .contact__role { font-size: 14px; margin-bottom: 12px; }
  .contact__line {
    display: flex; align-items: center; gap: 9px; font-size: 14px; margin-top: 6px;
  }
  .contact__line svg { width: 15px; height: 15px; flex: none; }
</style>
</head>
<body>
<main class="canvas">

  <section class="card card--front" aria-label="Card front">
    <div class="band band--top"></div>
    <div class="wordmark">
      <span class="wordmark__square"></span>
      <span class="wordmark__name">
        <span class="primary">quillbrook</span>
        <span class="secondary">NETWORKS LTD.</span>
      </span>
    </div>
    <div class="band band--bottom">
      <p class="tagline">Revolutionizing the way IT services are delivered</p>
    </div>
  </section>

  <section class="card card--back" aria-label="Card back">
    <div class="wordmark">
      <span class="wordmark__square"></span>
      <span class="wordmark__name">
        <span class="primary">quillbrook</span>
        <span class="secondary">NETWORKS LTD.</span>
      </span>
    </div>
    <div class="divider"></div>
    <div class="contact">
      <p class="contact__name">Dana Whitlock</p>
      <p class="contact__role">Network Engineer</p>
      <p class="contact__line">
        <svg viewBox="0 0 16 16" aria-hidden="true"><path fill="#35a8e0" d="M2 5c0-2 3-3 6-3s6 1 6 3v1h-3V5H5v1H2zM4 7h8l2 6H2z"/><circle cx="8" cy="10" r="1.6" fill="#fff"/></svg>
        604-555-0148
      </p>
      <p class="contact__line">
        <svg viewBox="0 0 16 16" aria-hidden="true"><rect x="1" y="3" width="14" height="10" fill="#35a8e0"/><path d="M1 3l7 6 7-6" fill="none" stroke="#fff" stroke-width="1.2"/></svg>
        dwhitlock@quillbrook.me
      </p>
      <p class="contact__line">
        <svg viewBox="0 0 16 16" aria-hidden="true"><circle cx="8" cy="8" r="6.5" fill="none" stroke="#35a8e0" stroke-width="1.3"/><ellipse cx="8" cy="8" rx="3" ry="6.5" fill="none" stroke="#35a8e0" stroke-width="1"/><path d="M1.5 8h13M2.5 5h11M2.5 11h11" stroke="#35a8e0" stroke-width="1"/></svg>
        www.quillbrook.me
      </p>
    </div>
  </section>

</main>
</body>
</html>
```